New Look and Feel for 82 year old Vantrek Ltd. presentations

We are seeking new ideas to have powerpoint-layouts for the group headquarters. Vantrek is an industrial company in maritime, hydraulics, heavy machinery and industrial services. Please read our history and watch the video for a quick familiarization. http://www.vantrek-example.fi/eng/main.php

Our customer relationships are based on trust, with Vantrek providing to customers, cooperation partners and other interest groups products and solutions that produce sustainable benefits.

Vantrek strives to ensure that the environmental impact of the products is considered over the entire life cycle and the processes used by the Group are as environmentally benign as possible.

Industry/Entity Type

It Company

Colors

Designer to choose colors to be used in the design.

Requirements
Must have
• Logo
Nice to have
• example animations and transitions

```html
<!DOCTYPE html>
<html lang="en">
<head>
<meta charset="utf-8">
<title>Vantrek presentation layouts</title>
<link rel="stylesheet" href="https://fonts.googleapis.com/css2?family=Oswald:wght@400;500;600&family=Montserrat:wght@600&family=Roboto:wght@400&display=swap">
<style>
:root{
  --red:#e2262d;
  --red-light:#ea4449;
  --red-deep:#b3060d;
  --ink:#2d2e33;
  --ink-soft:#3a3b40;
  --paper:#ececec;
  --white:#ffffff;
  --caption:#333333;
}
*{box-sizing:border-box;margin:0;padding:0}
html,body{width:1200px;height:1003px;overflow:hidden;background:var(--white)}
body{position:relative;font-family:'Roboto',Arial,sans-serif}
.page{position:absolute;width:704px;height:528px;transform:scale(.8);transform-origin:0 0;overflow:hidden;background:var(--paper);box-shadow:0 2px 6px rgba(0,0,0,.25)}
.page--cover{left:21px;top:23px}
.page--back{left:613px;top:23px}
.page--one{left:21px;top:506px;background:var(--ink)}
.page--two{left:613px;top:506px;background:var(--ink)}
.shapes{position:absolute;left:0;top:0;width:704px;height:528px}
.abs{position:absolute}
.display{font-family:'Oswald',Arial,sans-serif;font-weight:500;text-transform:uppercase;line-height:1.05}
.body-text{font-family:'Roboto',Arial,sans-serif;font-size:9px;line-height:1.38}
.justify{text-align:justify}
.accent{color:var(--red)}
.brand{font-family:'Oswald',Arial,sans-serif;font-weight:600;letter-spacing:1px;display:flex;align-items:center;gap:14px}
.brand__mark{display:inline-block;background:var(--red)}
.url{font-family:'Montserrat',Arial,sans-serif;font-weight:600;font-size:10.5px}
.footer-rule{position:absolute;height:1px}
.caption{position:absolute;width:563px;text-align:center;font-family:Arial,sans-serif;font-size:31px;color:var(--caption)}
.photo{position:absolute}
</style>
</head>
<body>

<!-- COVER -->
<section class="page page--cover">
  <svg class="shapes" viewBox="0 0 704 528">
    <rect x="0" y="116" width="704" height="49" fill="var(--red-deep)"/>
    <polygon points="0,0 140,0 205,165 0,165" fill="var(--red-deep)"/>
    <rect x="0" y="165" width="704" height="180" fill="var(--ink)"/>
    <polygon points="385,396 704,396 704,528 448,528" fill="var(--ink)"/>
    <polygon points="300,300 420,396 404,465 350,465" fill="var(--red-deep)"/>
    <polygon points="135,0 180,0 405,465 345,465" fill="var(--red-light)"/>
  </svg>
  <div class="photo" role="img" aria-label="Engineer grinding a large gear ring with sparks flying" style="left:235px;top:165px;width:469px;height:231px;background:linear-gradient(100deg,#1a1310 0%,#3a2410 30%,#7a5630 45%,#2a2c34 65%,#9a9ea6 85%,#c8cace 100%);clip-path:polygon(40px 0,100% 0,100% 100%,135px 100%)"></div>
  <svg class="shapes" viewBox="0 0 704 528" aria-hidden="true">
    <polygon points="215,165 235,165 335,396 312,396" fill="var(--red-light)"/>
  </svg>
  <div class="abs brand" style="left:300px;top:24px;font-size:44px;color:var(--ink)">
    <span class="brand__mark" style="width:30px;height:30px"></span>Vantrek
  </div>
  <h2 class="abs display" style="left:27px;top:226px;font-size:20px;color:var(--white)">Engineering Works</h2>
  <p class="abs body-text" style="left:27px;top:252px;width:190px;color:var(--white)">Vantrek Works is a business group which provides turnkey services of the mechanical engineering industry.</p>
  <h1 class="abs display" style="left:26px;top:382px;font-size:35px;color:var(--ink)">Lorem ipsum is<br>simply <span class="accent">dummy text</span></h1>
  <div class="abs display" style="left:18px;top:460px;width:283px;height:25px;background:#111;color:var(--white);font-size:17px;padding:2px 0 0 10px">2018 Lorem ipsum is simply dummy</div>
  <span class="footer-rule" style="left:425px;top:491px;width:128px;background:#999"></span>
  <svg class="abs" style="left:563px;top:483px" width="16" height="16" viewBox="0 0 16 16"><circle cx="8" cy="8" r="7" fill="none" stroke="#fff" stroke-width="1.4"/><ellipse cx="8" cy="8" rx="3" ry="7" fill="none" stroke="#fff" stroke-width="1.2"/><line x1="1" y1="8" x2="15" y2="8" stroke="#fff" stroke-width="1.2"/></svg>
  <span class="abs url" style="left:585px;top:484px;color:var(--white);font-size:10px">www.vantrek-example.fi</span>
</section>

<!-- BACK -->
<section class="page page--back">
  <svg class="shapes" viewBox="0 0 704 528">
    <rect x="0" y="0" width="704" height="165" fill="var(--red-deep)"/>
    <rect x="0" y="165" width="704" height="180" fill="var(--ink)"/>
  </svg>
  <div class="abs brand" style="left:0;top:48px;width:704px;justify-content:center;font-size:52px;color:var(--white)">Vantrek</div>
  <h2 class="abs display" style="left:0;top:200px;width:704px;text-align:center;font-size:27px;color:var(--white)">Lorem ipsum is<br><span class="accent" style="color:var(--red-light)">Lorem ipsum is simply</span></h2>
  <span class="abs" style="left:319px;top:266px;width:52px;height:2px;background:var(--white)"></span>
  <p class="abs body-text" style="left:170px;top:282px;width:364px;text-align:center;color:var(--white)">Lorem Ipsum is simply dummy text of the printing and typesetting industry. Lorem Ipsum has been the industry's standard dummy text ever since the 1500s</p>
  <p class="abs display" style="left:0;top:366px;width:704px;text-align:center;font-size:28px;color:var(--ink)"><span class="accent">Call us today</span>&nbsp; 020 555 0199</p>
  <p class="abs body-text" style="left:0;top:410px;width:704px;text-align:center;font-size:11.5px;color:var(--ink)">
    <svg width="9" height="11" viewBox="0 0 9 11" style="vertical-align:-1px"><path d="M4.5 0A4.5 4.5 0 0 0 0 4.5C0 8 4.5 11 4.5 11S9 8 9 4.5A4.5 4.5 0 0 0 4.5 0Z" fill="var(--ink)"/><circle cx="4.5" cy="4.5" r="1.6" fill="var(--paper)"/></svg>
    Vantrek Oy, Teollisuuskatu 8, PL 22</p>
  <p class="abs body-text" style="left:0;top:433px;width:704px;text-align:center;font-size:11.5px;color:var(--ink)">FI-26100 RAUMA</p>
  <span class="footer-rule" style="left:163px;top:494px;width:134px;background:var(--ink)"></span>
  <span class="abs url" style="left:297px;top:487px;width:110px;text-align:center;color:var(--ink);font-size:9.5px">www.vantrek-example.fi</span>
  <span class="footer-rule" style="left:407px;top:494px;width:134px;background:var(--ink)"></span>
</section>

<!-- PAGE 01 -->
<section class="page page--one">
  <div class="photo" role="img" aria-label="Young man with glasses working at a desk in a bright office" style="left:0;top:0;width:704px;height:528px;background:linear-gradient(160deg,#d8d2cc 0%,#b9aea4 35%,#6c6a6c 60%,#3a3b40 100%);clip-path:polygon(0 0,704px 0,704px 22px,0 505px)"></div>
  <svg class="shapes" viewBox="0 0 704 528">
    <line x1="704" y1="22" x2="0" y2="505" stroke="#fff" stroke-width="1.4"/>
    <polygon points="165,38 280,104 280,236 165,302 50,236 50,104" fill="none" stroke="rgba(255,255,255,.45)" stroke-width="16"/>
    <polygon points="165,46 273,108 273,232 165,294 57,232 57,108" fill="var(--red)" opacity=".92"/>
    <polyline points="100,100 165,62 230,100" fill="none" stroke="#fff" stroke-width="1.2"/>
    <polyline points="100,240 165,278 230,240" fill="none" stroke="#fff" stroke-width="1.2"/>
  </svg>
  <h2 class="abs display" style="left:75px;top:140px;font-size:30px;color:var(--white);line-height:1.12;font-weight:400">Lorem ipsum<br><span style="font-size:34px">Lorem ipsum</span></h2>
  <div class="photo" role="img" aria-label="Seagull in flight against a blue sky" style="left:312px;top:129px;width:149px;height:307px;background:linear-gradient(180deg,#3f6fb6 0%,#6f9ad3 45%,#a9c4e6 100%)"></div>
  <div class="abs" style="left:322px;top:268px;width:133px;height:157px;background:var(--white);padding:8px 8px">
    <h3 class="display" style="font-size:15px;color:var(--ink);font-weight:400">Lorem ipsum</h3>
    <p class="body-text justify" style="margin-top:9px;color:var(--ink);font-size:8.8px">Lorem Ipsum is simply dummy text of the printing and typesetting industry. Lorem Ipsum has been the industry's. Lorem Ipsum is simply dummy text of the printing and typesetting industry. Lorem Ipsum has been the industry's.</p>
  </div>
  <div class="abs" style="left:484px;top:196px;width:194px">
    <h3 class="display" style="font-size:16px;color:var(--white);font-weight:400">Lorem ipsum</h3>
    <p class="body-text justify" style="margin-top:6px;color:var(--white)">Lorem Ipsum is simply dummy text of the printing and typesetting industry. Lorem Ipsum has been the industry's.</p>
  </div>
  <span class="abs" style="left:484px;top:275px;width:194px;height:1px;background:var(--red)"></span>
  <div class="abs" style="left:484px;top:290px;width:194px">
    <h3 class="display" style="font-size:16px;color:var(--white);font-weight:400">Lorem ipsum</h3>
    <p class="body-text justify" style="margin-top:6px;color:var(--white)">Lorem Ipsum is simply dummy text of the printing and typesetting industry. Lorem Ipsum has been the industry's.</p>
  </div>
  <span class="abs" style="left:484px;top:370px;width:194px;height:1px;background:var(--red)"></span>
  <div class="abs" style="left:484px;top:387px;width:194px">
    <h3 class="display" style="font-size:16px;color:var(--white);font-weight:400">Lorem ipsum</h3>
    <p class="body-text justify" style="margin-top:6px;color:var(--white)">Lorem Ipsum is simply dummy text of the printing and typesetting industry. Lorem Ipsum has been the industry's.</p>
  </div>
  <span class="footer-rule" style="left:163px;top:494px;width:134px;background:#aaa"></span>
  <span class="abs url" style="left:297px;top:487px;width:110px;text-align:center;color:var(--white);font-size:9.5px">www.vantrek-example.fi</span>
  <span class="footer-rule" style="left:407px;top:494px;width:134px;background:#aaa"></span>
  <span class="abs url" style="left:664px;top:487px;color:var(--white);font-size:9.5px">01</span>
</section>

<!-- PAGE 02 -->
<section class="page page--two">
  <div class="abs" style="left:27px;top:43px;width:650px;height:429px;background:linear-gradient(90deg,#ffffff 0%,#f4f4f4 60%,#e6e6e6 100%)"></div>
  <span class="abs" style="left:50px;top:72px;width:2px;height:46px;background:var(--ink)"></span>
  <h2 class="abs display" style="left:56px;top:66px;font-size:31px;color:var(--ink);font-weight:400">Lorem ipsum</h2>
  <p class="abs display" style="left:56px;top:101px;font-size:16px;color:var(--red);font-weight:400">Lorem ipsum is simply</p>
  <p class="abs body-text justify" style="left:47px;top:143px;width:165px;color:var(--ink)">Lorem Ipsum is simply dummy text of the printing and typesetting industry. Lorem Ipsum has been the industry's standard dummy text ever since the 1500s, when an unknown printer took a galley of type and scrambled it to make a type specimen book. It has survive.</p>
  <p class="abs body-text justify" style="left:47px;top:255px;width:165px;color:var(--ink)">Lorem Ipsum is simply dummy text of the printing and typesetting industry. Lorem Ipsum has been the industry's standard dummy text ever since the 1500s, when an unknown printer took a galley of type and scrambled it to make a type specimen book. It has survived not only five centuries, but also the leap into electronic typesetting, remaining essentially unchanged. It was popularised in the 1960s with the release of Letraset sheets containing Lorem Ipsum passages, and more recently with desktop publishing.</p>
  <svg class="shapes" viewBox="0 0 704 528">
    <line x1="277" y1="100" x2="277" y2="420" stroke="var(--ink)" stroke-width="2"/>
    <g fill="var(--red)">
      <circle cx="277" cy="99" r="34"/><circle cx="277" cy="204" r="34"/>
      <circle cx="277" cy="311" r="34"/><circle cx="277" cy="419" r="34"/>
    </g>
    <g fill="#fff">
      <polygon points="277,84 293,111 261,111"/>
      <rect x="275.5" y="92" width="3" height="11" fill="var(--red)"/><rect x="275.5" y="105" width="3" height="3" fill="var(--red)"/>
      <polygon points="277,188 285,197 280,197 280,206 274,206 274,197 269,197"/>
      <rect x="264" y="209" width="12" height="3"/><rect x="264" y="214" width="12" height="3"/><rect x="278" y="211" width="12" height="3"/><rect x="278" y="216" width="12" height="3"/>
      <rect x="264" y="318" width="5" height="6"/><rect x="272" y="304" width="5" height="20"/><rect x="280" y="310" width="5" height="14"/><rect x="288" y="300" width="5" height="24"/>
      <polygon points="266,420 288,420 277,434"/>
    </g>
    <text x="277" y="419" text-anchor="middle" font-family="Oswald, Arial, sans-serif" font-size="18" font-weight="600" fill="#fff">$</text>
    <rect x="269" y="401" width="16" height="20" fill="none" stroke="#fff" stroke-width="2"/>
  </svg>
  <div class="abs" style="left:329px;top:66px;width:325px">
    <h3 class="display" style="font-size:15px;color:var(--ink);font-weight:400">Lorem ipsum</h3>
    <p class="body-text justify" style="margin-top:6px;color:var(--ink);font-size:8.8px">Lorem Ipsum is simply dummy text of the printing and typesetting industry. Lorem Ipsum has been the industry's standard dummy text ever since the 1500s, when an unknown printer took a galley of type and scrambled it to make a type specimen book. It has survive.</p>
  </div>
  <div class="abs" style="left:329px;top:170px;width:325px">
    <h3 class="display" style="font-size:15px;color:var(--ink);font-weight:400">Lorem ipsum</h3>
    <p class="body-text justify" style="margin-top:6px;color:var(--ink);font-size:8.8px">Lorem Ipsum is simply dummy text of the printing and typesetting industry. Lorem Ipsum has been the industry's standard dummy text ever since the 1500s, when an unknown printer took a galley of type and scrambled it to make a type specimen book. It has survive.</p>
  </div>
  <div class="abs" style="left:329px;top:276px;width:325px">
    <h3 class="display" style="font-size:15px;color:var(--ink);font-weight:400">Lorem ipsum</h3>
    <p class="body-text justify" style="margin-top:6px;color:var(--ink);font-size:8.8px">Lorem Ipsum is simply dummy text of the printing and typesetting industry. Lorem Ipsum has been the industry's standard dummy text ever since the 1500s, when an unknown printer took a galley of type and scrambled it to make a type specimen book. It has survive.</p>
  </div>
  <div class="abs" style="left:329px;top:384px;width:325px">
    <h3 class="display" style="font-size:15px;color:var(--ink);font-weight:400">Lorem ipsum</h3>
    <p class="body-text justify" style="margin-top:6px;color:var(--ink);font-size:8.8px">Lorem Ipsum is simply dummy text of the printing and typesetting industry. Lorem Ipsum has been the industry's standard dummy text ever since the 1500s, when an unknown printer took a galley of type and scrambled it to make a type specimen book. It has survive.</p>
  </div>
  <span class="footer-rule" style="left:163px;top:494px;width:134px;background:#aaa"></span>
  <span class="abs url" style="left:297px;top:487px;width:110px;text-align:center;color:var(--white);font-size:9.5px">www.vantrek-example.fi</span>
  <span class="footer-rule" style="left:407px;top:494px;width:134px;background:#aaa"></span>
  <span class="abs url" style="left:664px;top:487px;color:var(--white);font-size:9.5px">02</span>
</section>

<p class="caption" style="left:21px;top:458px">cover</p>
<p class="caption" style="left:613px;top:458px">back</p>
<p class="caption" style="left:21px;top:935px">page 01</p>
<p class="caption" style="left:613px;top:935px">page 02</p>

</body>
</html>
```